National appliance rental company needs a newspaper ad design

We need an ad template that we can use for different newspaper advertising. Ad is to be colourful - I have attached our current marketing so you have an idea of colours.
Text to be something like the below:

Want it, Rent it, Own it!

Need to update your furniture? Kids need stuff for school?

(Put in pics of phones and TV)

Zelvos starting from just $8 per week
Smart phones starting from $10 per week
Large family fridges from $30 per week

TV’s, laptops, whitegoods, furniture, beds – we will finance just about anything!

Fast approvals – call 1300 582 967 or go to www.brightwellhomeleasing.com.au/apply - NOW!
$50 credit voucher given to the first 10 successful applicants.

(Pic of logo somewhere)
Terms and conditions apply. Pricing based on 24 month term

Brightwell Home Leasing P/L ACN 061 847 293. Australian Credit Licence # 718294

Target Market(s)

Low income people and families

Industry/Entity Type

Appliance

Requirements
Must have
• I would love to have a couple of different sizes.
• Maybe 6cm x 10 cm, and also 10cms x 10cms.
Nice to have
• Please use the green from fridge magnet and colours from our logo, etc.

```html
<!DOCTYPE html>
<html lang="en">
<head>
<meta charset="utf-8">
<title>Brightwell Home Leasing – Newspaper Ad</title>
<link rel="stylesheet" href="https://fonts.googleapis.com/css2?family=Arimo:wght@400;700&family=Fredoka:wght@600&display=swap">
<style>
  :root {
    --red: #e0262b;
    --blue: #1277bd;
    --green: #7dba3f;
    --yellow: #fcc71b;
    --price-yellow: #ffe03a;
    --ink: #1b1b1b;
    --white: #ffffff;
    --stage: #ebe8e3;
    --body: "Arimo", Arial, sans-serif;
    --display: "Fredoka", "Arial Rounded MT Bold", sans-serif;
  }
  * { box-sizing: border-box; margin: 0; padding: 0; }
  html, body { width: 1200px; height: 1000px; overflow: hidden; background: var(--stage); }
  .ad {
    position: absolute; left: 113px; top: 18px; width: 964px; height: 962px;
    background: linear-gradient(#e6e6e6 0, #ffffff 260px);
    overflow: hidden; font-family: var(--body); color: var(--ink);
  }
  .mascot {
    position: absolute; left: 57px; top: 27px; width: 160px; height: 195px;
    background: linear-gradient(#f4f4f4, #cfcfcf); border-radius: 10px;
  }
  .brand { position: absolute; left: 230px; top: 80px; width: 360px; text-align: center; }
  .brand-name {
    font-family: var(--body); font-weight: 700; color: var(--red);
    font-size: 50px; line-height: 1.02; letter-spacing: -0.5px;
  }
  .brand-tagline { margin-top: 12px; font-style: italic; font-size: 19px; color: var(--ink); }
  .phones {
    position: absolute; left: 627px; top: 17px; width: 320px; height: 205px;
    background: linear-gradient(100deg, #dfe6ee 0%, #2a2a2a 40%, #2a2a2a 62%, #1f8fd6 100%);
    border-radius: 18px;
  }
  .tv {
    position: absolute; left: 652px; top: 197px; width: 265px; height: 260px;
    background: linear-gradient(#3a3a3a, #0e0e0e); border-radius: 4px;
  }
  .headline {
    position: absolute; left: 0; top: 262px; width: 534px; text-align: center;
    font-family: var(--display); font-weight: 600; font-size: 80px; line-height: 95px;
    color: var(--red); letter-spacing: -2px; white-space: nowrap;
    transform: scaleX(0.86); transform-origin: center top;
    -webkit-text-stroke: 3px var(--white); paint-order: stroke fill;
    text-shadow: 2px 4px 6px rgba(0,0,0,.35);
  }
  .questions {
    position: absolute; left: 120px; top: 477px; width: 404px; text-align: center;
    font-weight: 700; font-size: 19px; line-height: 25px;
  }
  .price {
    position: absolute; left: 18px; width: 332px; height: 68px; border-radius: 9px;
    color: var(--white); font-size: 25px; line-height: 29px; padding: 5px 0 0 25px;
  }
  .price strong { color: var(--price-yellow); }
  .price--red { top: 550px; background: var(--red); }
  .price--blue { top: 630px; background: var(--blue); }
  .price--green { top: 710px; background: var(--green); }
  .finance {
    position: absolute; left: 368px; top: 550px; width: 309px; height: 228px;
    background: var(--blue); border-radius: 9px; color: var(--white);
    font-size: 24.5px; line-height: 31px; text-align: center; padding: 24px 52px 0 0;
  }
  .voucher {
    position: absolute; left: 627px; top: 480px; width: 380px; height: 380px;
    border-radius: 50%; background: var(--yellow); border: 8px solid var(--white);
    color: var(--red); font-weight: 700; font-size: 36px; line-height: 42px;
    text-align: center; padding: 86px 26px 0 0;
  }
  .approvals {
    position: absolute; left: 0; top: 797px; width: 964px; height: 86px;
    background: var(--green); border-top: 4px solid var(--white); text-align: center;
  }
  .approvals-title {
    margin-top: 6px; font-weight: 700; font-size: 34px; line-height: 38px; color: var(--red);
    -webkit-text-stroke: 3px var(--white); paint-order: stroke fill;
  }
  .approvals-call { font-size: 22px; line-height: 30px; color: var(--ink); }
  .approvals-call strong { font-weight: 700; }
  .legal {
    position: absolute; left: 0; top: 897px; width: 964px; text-align: center;
    font-weight: 700; font-size: 19px; line-height: 25px;
  }
</style>
</head>
<body>
  <main class="ad">
    <div class="mascot" role="img" aria-label="Cartoon fridge mascot pointing upward"></div>

    <div class="brand">
      <div class="brand-name">Brightwell Home Leasing</div>
      <div class="brand-tagline">“It’s cheaper to lease smart!”</div>
    </div>

    <div class="phones" role="img" aria-label="Three smartphones fanned out with app screens"></div>
    <div class="tv" role="img" aria-label="Flat-screen television on a stand"></div>

    <h1 class="headline">Want it, Rent it,<br>Own it!</h1>

    <p class="questions">Need to update your furniture?<br>Kids need stuff for school?</p>

    <div class="price price--red">Zelvos starting from<br>just <strong>$8</strong> per week</div>
    <div class="price price--blue">Smart phones starting<br>from <strong>$10</strong> per week</div>
    <div class="price price--green">Large family fridges<br>from <strong>$30</strong> per week</div>

    <div class="finance">TV’s, laptops,<br>whitegoods,<br>furniture, beds –<br>we will finance<br>just about<br>anything!</div>

    <div class="voucher">$50 credit<br>voucher given<br>to the first<br>10 successful<br>applicants.</div>

    <section class="approvals">
      <div class="approvals-title">FAST APPROVALS</div>
      <div class="approvals-call">call <strong>1300 582 967</strong> or go to www.brightwellhomeleasing.com.au/apply - <strong>NOW!</strong></div>
    </section>

    <p class="legal">Terms and conditions apply. Pricing based on 24 month term<br>Brightwell Home Leasing P/L ACN 061 847 293. Australian Credit Licence # 718294</p>
  </main>
</body>
</html>
```